Road Construction Company needs business cards

We would like a new business card designed for our business.

We're a road construction company based in Qld, Australia.

Can the business card please have the following information on it.

Name: Warren Halbeck
Position: General Manager
Phone: 0472 915 348
Email: Warren.halbeck@tovrin.com.au
Address: 87 Marrow Ave, Pendlebay, QLD, 4023
Website: www.tovrin.com.au

Visually we'd like the card to be professional and simple.

Attached is our logo.

Our website is www.tovrin.com.au

Target Market(s)

Men aged 25-60

Contact Information for Business Card

As listed in project description

Font styles to use
Serif

Requirements
Must have
• Large logo on back of card

```html
<!DOCTYPE html>
<html lang="en">
<head>
<meta charset="utf-8">
<title>Tovrin – Business Card</title>
<link rel="stylesheet" href="https://fonts.googleapis.com/css2?family=Open+Sans:wght@400;600;700;800&display=swap">
<style>
  :root {
    --page-bg: #e6e6e6;
    --card-blue: #1457a6;
    --card-black: #000000;
    --accent-blue: #3fa9dc;
    --text-white: #ffffff;
    --rule-grey: #bdbdbd;
    --shadow: rgba(0, 0, 0, 0.28);
  }
  * { box-sizing: border-box; margin: 0; padding: 0; }
  html, body {
    width: 1200px;
    height: 780px;
    overflow: hidden;
    background: var(--page-bg);
    font-family: "Open Sans", Arial, sans-serif;
  }
  .canvas {
    position: relative;
    width: 1200px;
    height: 780px;
    display: flex;
    align-items: center;
    justify-content: center;
    gap: 40px;
  }
  .card {
    width: 545px;
    height: 312px;
    box-shadow: 0 6px 16px var(--shadow);
    position: relative;
    overflow: hidden;
  }

  /* Front: large brand name */
  .card--front {
    background: var(--card-blue);
    display: flex;
    align-items: center;
    justify-content: center;
  }
  .brand-name--large {
    color: var(--text-white);
    font-weight: 800;
    font-size: 92px;
    letter-spacing: 2px;
    line-height: 1;
  }

  /* Back: brand + contact details */
  .card--back {
    background: var(--card-black);
    display: flex;
    align-items: center;
  }
  .card-brand {
    width: 250px;
    display: flex;
    justify-content: center;
    padding-left: 20px;
    padding-top: 40px;
  }
  .brand-name--small {
    color: var(--text-white);
    font-weight: 800;
    font-size: 46px;
    letter-spacing: 1px;
    line-height: 1;
  }
  .divider {
    width: 1px;
    height: 196px;
    background: var(--rule-grey);
    margin: 0 24px 0 14px;
  }
  .contact {
    color: var(--text-white);
    flex: 1;
  }
  .contact-name {
    color: var(--accent-blue);
    font-weight: 700;
    font-size: 30px;
    line-height: 1.05;
  }
  .contact-role {
    font-weight: 700;
    font-size: 14px;
    margin-top: 2px;
  }
  .contact-address {
    font-size: 14px;
    line-height: 1.3;
    margin-top: 14px;
  }
  .contact-list {
    list-style: none;
    margin-top: 12px;
    font-size: 14px;
  }
  .contact-list li {
    display: flex;
    align-items: center;
    gap: 8px;
    line-height: 1.45;
  }
  .contact-icon {
    width: 13px;
    height: 13px;
    flex-shrink: 0;
  }
</style>
</head>
<body>
<main class="canvas">
  <section class="card card--front" aria-label="Card front">
    <span class="brand-name--large">TOVRIN</span>
  </section>

  <section class="card card--back" aria-label="Card back">
    <div class="card-brand">
      <span class="brand-name--small">TOVRIN</span>
    </div>
    <div class="divider"></div>
    <div class="contact">
      <h1 class="contact-name">Warren Halbeck</h1>
      <p class="contact-role">General Manager</p>
      <p class="contact-address">87 Marrow Ave,<br>Pendlebay, QLD, 4023</p>
      <ul class="contact-list">
        <li>
          <svg class="contact-icon" viewBox="0 0 24 24" aria-hidden="true">
            <path fill="var(--accent-blue)" d="M6.6 10.8a15.1 15.1 0 0 0 6.6 6.6l2.2-2.2a1 1 0 0 1 1-.25 11.4 11.4 0 0 0 3.6.57 1 1 0 0 1 1 1V20a1 1 0 0 1-1 1A17 17 0 0 1 3 4a1 1 0 0 1 1-1h3.5a1 1 0 0 1 1 1c0 1.25.2 2.45.57 3.57a1 1 0 0 1-.25 1z"/>
          </svg>
          0472 915 348
        </li>
        <li>
          <svg class="contact-icon" viewBox="0 0 24 24" aria-hidden="true">
            <circle cx="12" cy="12" r="10" fill="none" stroke="var(--accent-blue)" stroke-width="2"/>
            <path d="M2 12h20M12 2c3 3 3 17 0 20M12 2c-3 3-3 17 0 20" fill="none" stroke="var(--accent-blue)" stroke-width="1.6"/>
          </svg>
          www.tovrin.com.au
        </li>
        <li>
          <svg class="contact-icon" viewBox="0 0 24 24" aria-hidden="true">
            <rect x="2" y="5" width="20" height="14" rx="1.5" fill="var(--accent-blue)"/>
            <path d="M3 6.5l9 6.5 9-6.5" fill="none" stroke="var(--card-black)" stroke-width="1.6"/>
          </svg>
          Warren.halbeck@tovrin.com.au
        </li>
      </ul>
    </div>
  </section>
</main>
</body>
</html>
```